Torvane Email Signature Banners – Fabrication Capability Series

www.Torvane.com.au is an Australian engineering and fabrication company specialising in fabrication and welding of :
steel piping spools,
skids and frames,
small volume process steel tanks
and general steel fabrication
We require four distinct banner designs for use in Microsoft Lintaro email signatures. Each banner will highlight a specific capability while maintaining a consistent brand identity.
Deliverables
Four banners total:
Piping Spools Fabrication – focus on precision welding and stainless steel pipework
Skid & Frames Fabrication – highlight skid systems and structural frames
Small Steel Tanks Fabrication – show fabricated tanks and workshop craftsmanship
General Fabrication Solutions – broad steel fabrication theme for company-wide use
Dimensions: 600–700 px wide × 100 px high
Format: PNG (preferred), small file size prefered
Resolution: 72 dpi
Background: non-transparent, industrial or workshop setting
Text examples:
1. Piping Spools Fabrication
Option A: “Expert Fabrication Solutions for Process Piping”
Option B: “Precision Welding for Complex Systems”
Option C: “Delivering Quality in Every Spool”
Option D: “Engineered for Flow, Built for Strength”
2. Skid & Frames Fabrication
Option A: “Custom Engineered Modular Systems”
Option B: “Built Strong. Designed Smart.”
Option C: “Reliable Frames for Industrial Performance”
Option D: “Modular Fabrication for Seamless Integration”
3. Small Steel Tanks Fabrication
Option A: “Precision Built for Your Needs”
Option B: “Compact Strength. Proven Durability.”
Option C: “Fabricated for Performance and Longevity”
Option D: “Small Tanks. Big Reliability.”
4. General Fabrication Solutions
Option A: “Quality Craftsmanship, Proven Results”
Option B: “Your Partner in Precision Fabrication”
Option C: “Engineering Excellence in Every Weld”
Option D: “Australian Fabrication. Global Standards.”
Style Direction
Clean, professional, and engineering‑focused
Use Torvane brand colours
Blend photo realism with vector clarity (no heavy gradients)
Include subtle industrial textures or workshop imagery
Typography: bold sans‑serif, legible at small scale
Usage Context
These banners will appear at the bottom of staff email signatures via Lintaro Email Signature Tool for Microsoft 365, so clarity and fast loading are essential. No Logo is required in the banners.
Reference
Existing Torvane signature is attached. Colour palette to match the signature style and logo.
Target Market(s)
Engineering and construction companies,
Industry/Entity Type
Engineering fabrication design
Look and feel

```html
<!DOCTYPE html>
<html lang="en">
<head>
<meta charset="utf-8">
<title>Fabrication Banner – General Fabrication Solutions</title>
<link href="https://fonts.googleapis.com/css2?family=Montserrat:wght@500;700;800&display=swap" rel="stylesheet">
<style>
  :root {
    --blue-deep: #0b4fae;
    --blue-bright: #2b90e4;
    --white: #ffffff;
    --steel-dark: #1f2b3a;
    --steel-mid: #4d5d72;
    --steel-light: #8a9aac;
  }
  html, body {
    margin: 0;
    padding: 0;
    width: 1200px;
    height: 171px;
    overflow: hidden;
    background: var(--white);
  }
  .banner {
    position: relative;
    width: 1200px;
    height: 171px;
    overflow: hidden;
    font-family: "Montserrat", "Helvetica Neue", Arial, sans-serif;
  }
  .banner__shapes {
    position: absolute;
    inset: 0;
    width: 1200px;
    height: 171px;
  }
  .banner__copy {
    position: absolute;
    left: 691px;
    top: 15px;
    color: var(--white);
  }
  .banner__headline {
    margin: 0;
    font-size: 27px;
    line-height: 42px;
    letter-spacing: 0.2px;
    text-transform: uppercase;
  }
  .banner__headline-strong {
    display: block;
    font-weight: 800;
  }
  .banner__headline-light {
    display: block;
    font-weight: 500;
  }
  .banner__subline {
    margin: 12px 0 0;
    font-weight: 500;
    font-size: 24px;
    line-height: 28px;
  }
  .banner__code {
    position: absolute;
    right: 14px;
    bottom: 8px;
    color: var(--white);
    font-weight: 700;
    font-size: 10px;
    letter-spacing: 0.3px;
  }
</style>
</head>
<body>
  <div class="banner">
    <svg class="banner__shapes" viewBox="0 0 1200 171" xmlns="http://www.w3.org/2000/svg">
      <defs>
        <linearGradient id="panelBlue" x1="0" y1="0" x2="1" y2="0">
          <stop offset="0" stop-color="var(--blue-deep)"/>
          <stop offset="1" stop-color="var(--blue-bright)"/>
        </linearGradient>
        <linearGradient id="workshopTone" x1="0" y1="0" x2="0.6" y2="1">
          <stop offset="0" stop-color="var(--steel-light)"/>
          <stop offset="0.45" stop-color="var(--steel-mid)"/>
          <stop offset="1" stop-color="var(--steel-dark)"/>
        </linearGradient>
      </defs>
      <rect x="0" y="0" width="1200" height="171" fill="url(#panelBlue)"/>
      <polygon class="banner__photo" points="0,0 662,0 566,171 0,171" fill="url(#workshopTone)"
               role="img" aria-label="Photograph of stacked steel pipes in a fabrication workshop"/>
      <polygon class="banner__divider" points="662,0 688,0 592,171 566,171" fill="var(--white)"/>
    </svg>
    <div class="banner__copy">
      <h1 class="banner__headline">
        <span class="banner__headline-strong">Engineering Excellence</span>
        <span class="banner__headline-light">In Every Weld</span>
      </h1>
      <p class="banner__subline">General Fabrication Solutions</p>
    </div>
    <div class="banner__code">C62</div>
  </div>
</body>
</html>
```